Website for new dental office

I am Dr. Colin Ashford and am building a new dental practice. I specialize in general dentistry. I am young and have a higher end dental practice incorporating very new technologies and would like my website to reflect that. As many dental patients are older, the website must be very easy to navigate. I would like patients to be able to request appointments, and will eventually add on patient information forms (the health history, etc, that you normally fill out in the practice) from my practice management software, so leave an area for that.

Industry/Entity Type

Building

```html
<!DOCTYPE html>
<html lang="en">
<head>
<meta charset="utf-8">
<title>Ashford Dental Clinic</title>
<link href="https://fonts.googleapis.com/css2?family=Open+Sans:wght@400;600;700&display=swap" rel="stylesheet">
<style>
:root{
  --teal:#0aa6b8;
  --teal-dark:#087f8e;
  --teal-light:#3dbccb;
  --btn-dark:#0b6c78;
  --header-bg:#f3f3f3;
  --text:#555;
  --heading:#444;
  --grey-btn:#d9d9d9;
  --bubble:#8a8a8a;
  --line:#e2e2e2;
  --white:#fff;
}
*{box-sizing:border-box;margin:0;padding:0}
html,body{width:873px;height:1200px;overflow:hidden;background:var(--white)}
body{font-family:"Open Sans",sans-serif;color:var(--text);position:relative}
.abs{position:absolute}

/* top bar */
.topbar{left:0;top:0;width:873px;height:50px;background:var(--teal);color:var(--white);font-size:8px}
.topbar .contact-item{position:absolute;top:19px;display:flex;align-items:center;gap:6px}
.social{position:absolute;top:13px;width:24px;height:24px;background:#e4e4e4;border:1px solid #d0d0d0}
.social.active{background:#3f5f9c}

/* header */
.header{left:0;top:50px;width:873px;height:72px;background:var(--header-bg);border-bottom:1px solid #e6e6e6}
.logo{position:absolute;left:73px;top:20px;font-size:22px;font-weight:400;color:#777;letter-spacing:.2px}
.logo b{font-weight:600;color:var(--teal)}
.nav-item{position:absolute;top:0;height:72px;border-left:1px solid #e0e0e0;text-align:center;font-size:8px;color:#666;text-transform:uppercase}
.nav-item svg{display:block;margin:18px auto 6px}
.nav-item.current{color:var(--teal);font-weight:600;text-transform:none}
.nav-item.last{border-right:1px solid #e0e0e0}

/* hero */
.hero{left:0;top:122px;width:873px;height:361px;background:linear-gradient(100deg,#e9edef 0%,#dfe5e8 35%,#49b2cf 55%,#2aa6c8 80%,#d7e2e6 100%)}
.hero-arrow{position:absolute;top:162px;width:30px;height:30px;border:2px solid var(--white);border-radius:50%}
.hero-title{position:absolute;left:73px;top:188px;height:49px;padding:0 19px;background:var(--teal);color:var(--white);font-size:18px;line-height:49px;white-space:nowrap}
.hero-text{position:absolute;left:73px;top:256px;width:383px;height:84px;background:rgba(255,255,255,.88);padding:17px 18px;font-size:9.6px;line-height:14px;color:#555}
.dots{left:428px;top:493px;display:flex;gap:4px}
.dots span{width:6px;height:6px;border-radius:50%;background:#ccc}
.dots span.on{background:var(--teal)}

/* about */
.section-title{font-size:13.5px;font-weight:600;color:var(--teal);text-transform:uppercase}
.about-photo{left:74px;top:558px;width:95px;height:94px;background:linear-gradient(160deg,#e6ded6,#c9b4a4 55%,#eef0f2)}
.about-text{font-size:9.6px;line-height:13.2px;color:#555;text-align:justify}
.read-more{left:471px;top:720px;width:98px;height:21px;background:var(--grey-btn);font-size:9.5px;line-height:21px;text-align:center;color:#555}

/* appointment */
.appointment{left:585px;top:530px;width:216px;height:210px;background:var(--teal)}
.appointment h3{position:absolute;left:0;top:10px;width:100%;text-align:center;color:var(--white);font-size:11.5px;font-weight:600;letter-spacing:.3px}
.field{position:absolute;background:var(--white);font-size:6.5px;color:#888;padding:0 7px;display:flex;align-items:center;justify-content:space-between;text-transform:uppercase}
.book{position:absolute;left:28px;top:176px;width:161px;height:20px;background:var(--btn-dark);color:var(--white);font-size:8px;font-weight:600;text-align:center;line-height:20px}

/* blogs */
.block-title{font-size:16px;font-weight:400;color:#333}
.block-title span{color:var(--teal)}
.rule{height:1px;background:var(--line)}
.circ{position:absolute;width:15px;height:15px;border-radius:50%}
.circ.grey{background:#bdbdbd}
.circ.teal{background:var(--teal)}
.date-box{position:absolute;width:33px;height:34px;background:#eee;text-align:center;color:#444}
.date-box .day{font-size:13px;font-weight:700;line-height:16px;display:block;margin-top:4px}
.date-box .mon{font-size:6.5px;font-weight:600;display:block}
.blog-title{position:absolute;font-size:11px;line-height:16.5px;color:#444}
.blog-img{position:absolute;width:220px;height:106px}
.blog-text{position:absolute;width:222px;font-size:9.3px;line-height:13.6px;color:#555}
.blog-text a{color:var(--teal);text-decoration:none}

/* testimonials */
.avatar{position:absolute;width:40px;height:40px;border-radius:50%;border:2px solid #ddd;background:linear-gradient(135deg,#f1d9c7,#c9906e)}
.who{position:absolute;font-size:6.5px;line-height:8px;color:#444}
.who b{font-weight:700;font-size:7px}
.bubble{position:absolute;left:645px;width:156px;height:58px;background:var(--bubble);color:var(--white);font-size:7.5px;line-height:12px;padding:8px 7px 0 7px;text-align:justify;border-bottom:2px solid #c9c9c9}
.bubble::before{content:"";position:absolute;left:-10px;top:0;border-top:10px solid var(--bubble);border-left:10px solid transparent}

/* footer */
.footer{left:0;top:1128px;width:873px;height:72px;background:var(--teal-light)}
.footer .links{position:absolute;top:12px;font-size:9.5px;color:var(--white)}
.footer .bottom{position:absolute;left:0;top:36px;width:873px;height:36px;background:#35b3c3}
.footer .copy{position:absolute;left:0;top:11px;width:873px;text-align:center;font-size:9px;color:var(--white)}
.to-top{position:absolute;left:776px;top:24px;width:25px;height:25px;border:1px solid var(--white)}
</style>
</head>
<body>

<div class="abs topbar">
  <div class="contact-item" style="left:75px">
    <svg width="12" height="14" viewBox="0 0 12 14"><path d="M3 1 L5 4 L4 6 Q5 9 8 10 L10 9 L11 12 Q9 14 6 12 Q1 8 1 3 Z" fill="#fff"/></svg>
    <span>Call Us: (20) 5550-1942</span>
  </div>
  <div class="contact-item" style="left:198px">
    <svg width="16" height="11" viewBox="0 0 16 11"><rect x=".5" y=".5" width="15" height="10" fill="none" stroke="#fff"/><path d="M.5 .5 L8 6 L15.5 .5" fill="none" stroke="#fff"/></svg>
    <span>hello@ashforddental.example</span>
  </div>
  <div class="social" style="left:705px"></div>
  <div class="social active" style="left:729px"></div>
  <div class="social" style="left:753px"></div>
  <div class="social" style="left:777px"></div>
</div>

<header class="abs header">
  <div class="logo"><b>Ashford</b> Dental Clinic</div>
  <div class="nav-item" style="left:377px;width:83px">
    <svg width="22" height="20" viewBox="0 0 22 20"><path d="M11 1 L21 10 H18 V19 H13 V13 H9 V19 H4 V10 H1 Z" fill="#777"/></svg>Home
  </div>
  <div class="nav-item" style="left:460px;width:82px">
    <svg width="18" height="20" viewBox="0 0 18 20"><rect x="2" y="1" width="14" height="18" rx="1" fill="#777"/><rect x="5" y="5" width="8" height="1.5" fill="#eee"/><rect x="5" y="9" width="8" height="1.5" fill="#eee"/><rect x="5" y="13" width="8" height="1.5" fill="#eee"/></svg>Blog
  </div>
  <div class="nav-item current" style="left:542px;width:83px">
    <svg width="16" height="22" viewBox="0 0 16 22"><path d="M3 7 Q3 2 8 2 Q13 2 13 7 Q13 10 9 12 V15" fill="none" stroke="#0aa6b8" stroke-width="3"/><rect x="7" y="17.5" width="4" height="4" fill="#0aa6b8"/></svg>Help
  </div>
  <div class="nav-item" style="left:625px;width:91px;text-transform:none">
    <svg width="22" height="22" viewBox="0 0 22 22"><circle cx="9" cy="9" r="5" fill="none" stroke="#777" stroke-width="3.5" stroke-dasharray="2.5 1.4"/><circle cx="16" cy="16" r="3.2" fill="none" stroke="#777" stroke-width="2.5" stroke-dasharray="1.6 1"/></svg>Gallery
  </div>
  <div class="nav-item last" style="left:716px;width:82px">
    <svg width="26" height="20" viewBox="0 0 26 20"><path d="M2 7 Q13 -1 24 7 L21 9 L18 6 H8 L5 9 Z" fill="#777"/><path d="M6 10 H20 L22 18 H4 Z" fill="#777"/><circle cx="13" cy="14" r="2.5" fill="#eee"/></svg>Contact
  </div>
</header>

<section class="abs hero" role="img" aria-label="Bright dental treatment room with a patient chair, tools and a blue wall">
  <div class="hero-arrow" style="left:19px"><svg width="26" height="26" viewBox="0 0 26 26"><path d="M15 8 L10 13 L15 18" fill="none" stroke="#fff" stroke-width="1.5"/></svg></div>
  <div class="hero-arrow" style="left:823px"><svg width="26" height="26" viewBox="0 0 26 26"><path d="M11 8 L16 13 L11 18" fill="none" stroke="#fff" stroke-width="1.5"/></svg></div>
  <div class="hero-title">ASHFORD DENTAL CLINIC</div>
  <div class="hero-text">Pellentesque dolor metus, auctor quis elementum vitae, ullamcorper a erat. Etiam molestie ornare eleifend. Integer ultricies magna vel augue convallis eu mattis est lobortis. Aenean pulvinar sapien a leo hendrerit a convallis</div>
</section>
<div class="abs dots"><span class="on"></span><span></span><span></span></div>

<section>
  <h2 class="abs section-title" style="left:74px;top:528px">About Us</h2>
  <div class="abs about-photo" role="img" aria-label="Portrait photo of the lead dentist"></div>
  <p class="abs about-text" style="left:186px;top:553px;width:383px">Our services are the culmination of 15 years of experience of Dr. Martin Keller, PT, DPT, MS in the sports and orthopedic physical therapy arena. Martin directed the rehabilitation services for the largest orthopedic group in Chester County. He has provided the services for an orthopedic and sports medicine group that had specialists in spine, shoulder, elbow, wrist, hand, hip, knee,</p>
  <p class="abs about-text" style="left:186px;top:633px;width:383px">Ankle and foot surgery and treatment. His expertise is the treatment of any and all sports and orthopedic injuries, whether they are the result of trauma,</p>
  <p class="abs about-text" style="left:74px;top:663px;width:495px;text-align:left">repetitive movements or postures or the result of a surgical intervention. Martin Keller, PT, DPT, MS is confident that his extensive knowledge base and manual skills will drive Harborview Sports &amp; Orthopedic Physical Therapy to become a keystone in the private practice physical therapy community.</p>
  <div class="abs read-more">Read More</div>
</section>

<form class="abs appointment">
  <h3>SCHEDULE AN APPOINTMENT</h3>
  <div class="field" style="left:28px;top:32px;width:161px;height:18px">Name</div>
  <div class="field" style="left:28px;top:57px;width:161px;height:18px">Email ID</div>
  <div class="field" style="left:28px;top:82px;width:161px;height:18px">Phone Number</div>
  <div class="field" style="left:28px;top:107px;width:77px;height:18px">Date
    <svg width="8" height="8" viewBox="0 0 8 8"><rect x=".5" y="1" width="7" height="6.5" fill="none" stroke="#bbb"/><rect x=".5" y="1" width="7" height="2" fill="#bbb"/></svg></div>
  <div class="field" style="left:112px;top:107px;width:77px;height:18px">Time
    <svg width="8" height="8" viewBox="0 0 8 8"><circle cx="4" cy="4" r="3.5" fill="#999"/><path d="M4 2 V4 H6" stroke="#fff" fill="none"/></svg></div>
  <div class="field" style="left:28px;top:131px;width:161px;height:34px;align-items:flex-start;padding-top:5px">Write your message</div>
  <div class="book">BOOK NOW</div>
</form>

<section>
  <h2 class="abs block-title" style="left:72px;top:782px"><span>Recent</span> Blogs</h2>
  <div class="abs rule" style="left:73px;top:812px;width:473px"></div>
  <div class="circ grey" style="left:510px;top:789px"></div>
  <div class="circ teal" style="left:533px;top:789px"></div>

  <div class="date-box" style="left:73px;top:834px"><span class="day">21</span><span class="mon">SEP</span></div>
  <div class="blog-title" style="left:114px;top:833px;width:175px">Magna Mollis Ultricies Euismod Fermentum Elit</div>
  <div class="blog-img" style="left:73px;top:883px;background:linear-gradient(120deg,#1f6f7c,#e7d8cd 55%,#c9d1d6)" role="img" aria-label="Dentist treating a patient with an assistant"></div>
  <p class="blog-text" style="left:73px;top:1001px">Cras justo odio, dapibus ac facilisis in, egestas eget quam. Integer posuere erat ante venenatis dapibus posuere velit aliquet.</p>

  <div class="date-box" style="left:325px;top:834px"><span class="day">20</span><span class="mon">SEP</span></div>
  <div class="blog-title" style="left:366px;top:833px;width:175px">Ornare Nullam Risus Mollis Parturient</div>
  <div class="blog-img" style="left:325px;top:883px;background:linear-gradient(110deg,#3d4a5a,#d8b8a4 45%,#9aa6b4)" role="img" aria-label="Patient relaxing in a dental chair"></div>
  <p class="blog-text" style="left:325px;top:1001px">Vivamus sagittis lacus vel augue laoreet rutrum faucibus dolor auctor. Morbi leo risus, porta ac consectetur ac, <a>vestibulum</a> at eros.</p>
</section>

<section>
  <h2 class="abs block-title" style="left:579px;top:787px"><span>What</span> people say</h2>
  <div class="abs rule" style="left:579px;top:813px;width:223px"></div>
  <div class="circ grey" style="left:763px;top:789px"></div>
  <div class="circ teal" style="left:786px;top:789px"></div>

  <div class="avatar" style="left:579px;top:838px" role="img" aria-label="Customer photo"></div>
  <div class="who" style="left:579px;top:880px"><b>SARAH DOE</b><br>CEO, NORTHWIND</div>
  <div class="bubble" style="top:839px">Because we know you don't want to be limited on a portrait or scape format we made Showcase.</div>

  <div class="avatar" style="left:579px;top:922px" role="img" aria-label="Customer photo"></div>
  <div class="who" style="left:579px;top:965px"><b>SARAH DOE</b><br>CEO, NORTHWIND</div>
  <div class="bubble" style="top:924px">Because we know you don't want to be limited on a portrait or scape format we made Showcase.</div>

  <div class="avatar" style="left:579px;top:1010px" role="img" aria-label="Customer photo"></div>
  <div class="who" style="left:579px;top:1052px"><b>SARAH DOE</b><br>CEO, NORTHWIND</div>
  <div class="bubble" style="top:1011px">Because we know you don't want to be limited on a portrait or scape format we made Showcase.</div>
</section>

<footer class="abs footer">
  <span class="links" style="left:274px">Home</span>
  <span class="links" style="left:330px">Features</span>
  <span class="links" style="left:398px">Shop</span>
  <span class="links" style="left:450px">Blog</span>
  <span class="links" style="left:499px">Work</span>
  <span class="links" style="left:554px">Contact</span>
  <div class="bottom">
    <div class="copy">Ashford dental clinic © 2014 All Rights Reserved.</div>
  </div>
  <div class="to-top"><svg width="23" height="23" viewBox="0 0 23 23"><path d="M8 13 L11.5 9.5 L15 13" fill="none" stroke="#fff" stroke-width="1.3"/></svg></div>
</footer>

</body>
</html>
```